Design a Job Application & CV

I need a design for upcoming job applications that includes a cv. It needs to look as elegant and modern as possible as the application will be send mainly to large corporations and strategy consultancies. I have attached an application that I like for your consideration. One of the more difficult requirements is that it needs to be editable in ms office word for mac/windows.
As stated only the design is part of this project. I will fill in my content later on.
Reason: Dear Designers,
I am going to increase the budget as well as extending the deadline. I am hoping that you can improve upon the design that I have provided in the brief. If you have questions please let me know.
Dear Designers,
Target Market(s)
Human Resources Managers, Senior Consultants and Executives of larger firms
Industry/Entity Type
Office
Requirements
Must have
- 4 Pages including( a cover page, a coverletter page, 2 pages cv)
It should be easy to edit and should be readable by word for mac, i.e. in the *.docx format.
Here is an example of what I like:
http://www.torvenmald.example/applicationexample.pdf
http://www.torvenmald.example/applicationExample.docx
colors that I like are blue, grey, black, white
Nice to have
- icons to indicate sections
Should not have
- invasive cliparts

```html
<!DOCTYPE html>
<html lang="en">
<head>
<meta charset="utf-8">
<title>Coverletter</title>
<link rel="stylesheet" href="https://fonts.googleapis.com/css2?family=Didact+Gothic&family=Tenor+Sans&display=swap">
<style>
  :root {
    --brand-blue: #0aa3dc;
    --charcoal-dark: #3a3a3c;
    --charcoal-light: #8a8a8c;
    --ink: #4a4a4a;
    --paper: #ffffff;
  }
  html, body {
    margin: 0;
    padding: 0;
    overflow: hidden;
    background: var(--paper);
  }
  .page {
    position: relative;
    width: 848px;
    height: 1200px;
    overflow: hidden;
    background: var(--paper);
    font-family: "Didact Gothic", "Helvetica Neue", Arial, sans-serif;
    color: var(--ink);
  }
  .header-shade {
    position: absolute;
    left: 0; top: 0;
    width: 100%; height: 54px;
    background: linear-gradient(90deg, var(--charcoal-dark) 0%, #555557 60%, var(--charcoal-light) 100%);
  }
  .header-band {
    position: absolute;
    left: 0; top: 54px;
    width: 100%; height: 62px;
    background: var(--brand-blue);
  }
  .header-band .dots {
    position: absolute;
    left: 0; width: 100%; height: 0;
    border-top: 2px dotted rgba(255,255,255,0.85);
  }
  .header-band .dots.top { top: 5px; }
  .header-band .dots.bottom { bottom: 5px; }
  .page-title {
    position: absolute;
    left: 50px; top: 11px;
    margin: 0;
    font-family: "Tenor Sans", "Helvetica Neue", Arial, sans-serif;
    font-weight: 400;
    font-size: 34px;
    line-height: 40px;
    color: var(--paper);
  }
  .letter {
    position: absolute;
    left: 46px; top: 184px;
    width: 758px;
    font-size: 17.5px;
    line-height: 39px;
  }
  .letter p { margin: 0; text-align: justify; }
  .salutation { margin-bottom: 30px !important; }
  .letter .body-para { margin-bottom: 38px; }
  .letter .body-para.last { margin-bottom: 0; }
  .footer-band {
    position: absolute;
    left: 0; top: 1152px;
    width: 100%; height: 28px;
    background: var(--brand-blue);
  }
  .footer-shade {
    position: absolute;
    left: 0; top: 1180px;
    width: 100%; height: 20px;
    background: linear-gradient(90deg, var(--charcoal-dark) 0%, #555557 60%, var(--charcoal-light) 100%);
  }
</style>
</head>
<body>
<main class="page">
  <div class="header-shade"></div>
  <header class="header-band">
    <div class="dots top"></div>
    <h1 class="page-title">Coverletter</h1>
    <div class="dots bottom"></div>
  </header>

  <article class="letter">
    <p class="salutation">Dear Folks</p>
    <p class="body-para">Lorem ipsum dolor sit amet, consectetur adipiscing elit. Quisque dictum leo quis mauris dictum auctor. Praesent viverra, elit at rutrum fringilla, purus nisl feugiat est, sit amet lobortis magna mauris id nibh. Sed interdum massa non mauris faucibus cursus. Integer at tellus sit amet lacus ultrices ullamcorper. Nunc vel libero dui, sit amet pellentesque ligula. Suspendisse semper, urna.</p>
    <p class="body-para">Aenean quis nisi arcu, blandit mollis odio. Vestibulum nulla enim, viverra a auctor quis, suscipit rhoncus libero. Donec quis libero vel magna luctus pulvinar. Duis eget nulla vel massa commodo semper placerat id leo. Nunc eu leo sed quam hendrerit accumsan. Maecenas eleifend nisi non velit dignissim ut suscipit arcu imperdiet. Phasellus nisi nulla, tincidunt. Proin tincidunt, est sed rhoncus mattis, nunc sem aliquet quam, eget tristique augue dolor vel orci. Vestibulum et tellus dui, vitae sollicitudin sapien. Pellentesque nisl tortor, faucibus in mollis non, dignissim et felis.</p>
    <p class="body-para last">Phasellus nisi nulla, tincidunt. Proin tincidunt, est sed rhoncus mattis, nunc sem aliquet quam, eget tristique augue dolor vel orci. Vestibulum et tellus dui, vitae sollicitudin sapien. Pellentesque nisl tortor, faucibus in mollis non, dignissim<br>et felis.</p>
    <p class="closing">Sincerely,</p>
    <p class="signature">Good Looking</p>
  </article>

  <div class="footer-band"></div>
  <div class="footer-shade"></div>
</main>
</body>
</html>
```